Landscape Construction and Design Company

We are a landscape construction and design company from New Jersey. We design and install landscapes and hardscapes for residential properties. The name of the company is Belwick's Landscape and Design LLC. We specialize mostly in planting trees and stone work, some water features. We would like to see design themes that include a tree or trees and a stone walkway or wall. We like earth tone colors. We like traditional to modern designs.

Target Market(s)

Homeowners

Industry/Entity Type

Landscape

Contact Information for Business Card

Nature themed design, earth tone colors, space for company name, address, phone numbers, email and website address

Logo Text

No text

Font styles to use
Serif

Colors

Designer to choose colors to be used in the design.

Requirements
Must have
• A tree or trees, similar to the ones uploaded in my supporting images
Nice to have
• I like trees similar to those in my uploaded supporting images. I like artistic, nature theme, earth tone colors
Should not have
• Pictures of real landscapes, cartoon looking logo or objects

```html
<!DOCTYPE html>
<html lang="en">
<head>
<meta charset="utf-8">
<title>Belwick's Landscape and Design LLC — Business Cards</title>
<link rel="stylesheet" href="https://fonts.googleapis.com/css2?family=Cinzel:wght@500;600&family=Lato:wght@400&display=swap">
<style>
  :root {
    --backdrop: #4a413c;
    --card: #131313;
    --leaf-green: #6fb52c;
    --bark-red: #8a2a22;
    --text-light: #f1f1f1;
    --text-muted: #c9c9c9;
    --divider: #3a3a3a;
  }
  * { margin: 0; padding: 0; box-sizing: border-box; }
  html, body {
    width: 1200px; height: 900px; overflow: hidden;
    background: var(--backdrop);
  }
  .canvas {
    position: relative; width: 1200px; height: 900px;
  }
  .card {
    position: absolute;
    width: 525px; height: 300px;
    background: var(--card);
    box-shadow: 0 10px 30px rgba(0,0,0,0.45);
  }
  .card--contact { left: 60px; top: 330px; }
  .card--brand { left: 615px; top: 270px; }

  /* Contact side */
  .brand-block {
    position: absolute; left: 40px; top: 0; width: 220px; height: 300px;
    display: flex; align-items: center; justify-content: center; gap: 12px;
  }
  .brand-mark {
    width: 14px; height: 14px; border-radius: 50%;
    background: var(--leaf-green); flex: none;
  }
  .brand-name {
    font-family: "Cinzel", serif; font-weight: 600;
    color: var(--leaf-green);
    font-size: 22px; line-height: 1.25; letter-spacing: 0.5px;
  }
  .contact-divider {
    position: absolute; left: 285px; top: 60px; width: 1px; height: 180px;
    background: var(--divider);
  }
  .contact-block {
    position: absolute; left: 305px; top: 62px; right: 20px;
    font-family: "Lato", sans-serif; color: var(--text-light);
  }
  .person-name {
    font-family: "Cinzel", serif; font-weight: 500;
    color: var(--leaf-green); font-size: 17px; letter-spacing: 0.5px;
  }
  .person-role { font-size: 13px; margin-bottom: 10px; }
  .contact-list { list-style: none; font-size: 13px; line-height: 1.55; }
  .contact-list li { display: flex; align-items: center; gap: 7px; }
  .contact-list svg { width: 11px; height: 11px; flex: none; fill: var(--leaf-green); }
  .address { margin-top: 12px; font-size: 13px; line-height: 1.45; }

  /* Brand side */
  .brand-front {
    position: absolute; left: 0; right: 0; top: 95px;
    display: flex; align-items: center; justify-content: center; gap: 14px;
  }
  .brand-front .brand-name { font-size: 24px; text-align: left; }
  .services {
    position: absolute; left: 0; right: 0; top: 205px; text-align: center;
    font-family: "Lato", sans-serif; font-size: 13px; letter-spacing: 0.5px;
    color: var(--text-muted); text-transform: uppercase;
  }
  .services .sep { color: var(--leaf-green); margin: 0 5px; }
</style>
</head>
<body>
<main class="canvas">

  <section class="card card--contact" aria-label="Business card, contact side">
    <div class="brand-block">
      <span class="brand-mark"></span>
      <p class="brand-name">Belwick's<br>Landscape and<br>Design LLC</p>
    </div>
    <div class="contact-divider"></div>
    <div class="contact-block">
      <p class="person-name">DANIEL HARLOW</p>
      <p class="person-role">Managing Director</p>
      <ul class="contact-list">
        <li><svg viewBox="0 0 24 24" aria-hidden="true"><path d="M6.6 10.8a15.1 15.1 0 0 0 6.6 6.6l2.2-2.2a1 1 0 0 1 1-.25 11.4 11.4 0 0 0 3.6.57 1 1 0 0 1 1 1V20a1 1 0 0 1-1 1A17 17 0 0 1 3 4a1 1 0 0 1 1-1h3.5a1 1 0 0 1 1 1c0 1.25.2 2.45.57 3.57a1 1 0 0 1-.25 1z"/></svg>555 201 3478</li>
        <li><svg viewBox="0 0 24 24" aria-hidden="true"><path d="M2 5h20v14H2z M2 5l10 8 10-8" fill="none" stroke="#6fb52c" stroke-width="2.5"/></svg>info@belwickland.com</li>
        <li><svg viewBox="0 0 24 24" aria-hidden="true"><circle cx="12" cy="12" r="10"/><path d="M2 12h20M12 2c3 3 3 17 0 20M12 2c-3 3-3 17 0 20" stroke="#131313" stroke-width="1.6" fill="none"/></svg>www.belwickland.com</li>
      </ul>
      <p class="address">88 Orchard Lane,<br>Millbrook, NJ 07001</p>
    </div>
  </section>

  <section class="card card--brand" aria-label="Business card, brand side">
    <div class="brand-front">
      <span class="brand-mark"></span>
      <p class="brand-name">Belwick's<br>Landscape and Design LLC</p>
    </div>
    <p class="services">Planting Trees<span class="sep">|</span>Stone Work<span class="sep">|</span>Water Features</p>
  </section>

</main>
</body>
</html>
```